Brand Identity & Marketing Website Design for Professional Football Scouting Software

Merivantalo is a professional football scouting report generation software.
It is a standalone desktop application that allows football clubs, agencies and players to generate structured, executive-level A4 PDF scouting reports.
This is NOT:
a betting platform
a fan website
a football news blog
a SaaS subscription platform
This is a premium document-generation software tool designed for professional use inside football organizations.
The brand must reflect:
• Structure
• Authority
• Precision
• Professionalism
• Trust
• Executive-level quality
Think consulting firm, performance analysis tool, structured business software.
Not flashy sports media.
What We Need
We are looking for:
1️⃣ Logo Design
2️⃣ Full Brand Identity System
3️⃣ Marketing Website UI/UX Design
(Development is NOT included in this job.)
Important Product Context
Merivantalo is sold as a one-time purchase software package.
After purchase: • Customers download the software
• Install it locally
• Generate reports offline
There is no recurring subscription.
There is no SaaS login platform.
The website is a marketing and purchase website only.
1️⃣ Logo Design
The logo must:
• Be professional and timeless
• Work in both light and dark backgrounds
• Be scalable (website header, app icon, favicon)
• Avoid cliché football logo styles (no shields, mascots, flashy emblems)
• Feel modern, clean, and strong
We prefer:
• Clean typography-based logo
• Minimal symbol integration
• Strong visual balance
• Suitable for software branding
Name:
Merivantalo
Optional tagline:
The leading platform for professional football scouting reports
Deliver:
• Full logo
• Icon-only version (for desktop app icon)
• Light & dark variations
2️⃣ Brand Identity System
We need a structured design system that supports:
• Marketing website
• Desktop application UI
• PDF report previews
Please define:
• Primary color palette
• Secondary color palette
• Accent colors
• Typography system (professional, highly readable)
• Heading hierarchy
• UI styling guidelines
• Light mode & dark mode principles
The design must feel:
• Minimal
• Grid-based
• Clean
• Premium
• Corporate
Avoid:
• Neon colors
• Heavy gradients
• Overly sporty visuals
• Gaming aesthetics
3️⃣ Marketing Website Design (UI/UX Only)
We need full website design in Figma for:
• Homepage
• Product Overview
• Packages Page (Club / Agency / Player)
• How It Works
• Demo Section
• FAQ
• Contact
• Purchase / Download Page
Design must include:
• Hero section
• Feature explanation sections
• Structured benefits
• Product screenshots placement
• Pricing comparison layout
• Clear call-to-action areas
• Professional footer
Responsive design required (Desktop-first, mobile adaptation).
Important:
Content copy will be provided by us.
Designer focuses on layout, structure, hierarchy and visual design.
Target Audience
• Professional football clubs
• Scouting departments
• Player agencies
• Semi-professional and professional players
This is primarily B2B, with some B2C.
Style Direction
We are looking for:
• Strong typography
• Balanced whitespace
• Structured layouts
• Subtle but confident use of color
• Professional photography (if used)
• Premium software feel
The website and brand must feel trustworthy and high-level.
Deliverables
• Logo files (AI, SVG, PNG)
• Brand guideline document (PDF)
• Figma file with full website UI
• Icon assets (app icon, favicon)
• Color and typography system

Need extra days to review

```html
<!DOCTYPE html>
<html lang="en">
<head>
<meta charset="utf-8">
<title>Merivantalo — Professional Football Scouting Reports</title>
<link rel="stylesheet" href="https://fonts.googleapis.com/css2?family=Montserrat:wght@300;400;500;600;700;800&display=swap">
<style>
:root{
  --navy:#141d4f;
  --navy-deep:#0e1538;
  --primary:#1f2b7a;
  --ink:#1b1f33;
  --muted:#5b6178;
  --line:#d9dde9;
  --tint:#e4e9f7;
  --tint-soft:#f3f5fb;
  --white:#ffffff;
  --green:#2fd17a;
}
*{box-sizing:border-box;margin:0;padding:0}
html,body{width:1200px;height:4532px;overflow:hidden}
body{font-family:"Montserrat",sans-serif;color:var(--ink);background:var(--white);position:relative}
.abs{position:absolute}
.btn{display:inline-block;font-weight:700;font-size:12px;letter-spacing:.04em;padding:10px 18px;border-radius:4px;text-transform:uppercase}
.btn-navy{background:var(--navy);color:var(--white)}
.btn-white{background:var(--white);color:var(--navy)}
.section-title{font-size:46px;font-weight:300;color:var(--ink);text-align:center}
.section-title b{font-weight:700}
.brand{display:flex;align-items:center;gap:10px;font-weight:700;font-size:21px}
.brand-square{width:30px;height:30px;border-radius:6px;background:var(--navy)}

/* header */
.site-header{top:0;left:0;width:1200px;height:64px;background:var(--white);display:flex;align-items:center;padding:0 120px;justify-content:space-between;border-bottom:1px solid var(--line)}
.site-nav{display:flex;gap:30px;font-size:13px;font-weight:500;align-items:center}
.site-nav .active{font-weight:700;border-bottom:2px solid var(--navy);padding-bottom:3px}

/* hero */
.hero{top:64px;left:0;width:1200px;height:656px;background:linear-gradient(100deg,#0d1220 0%,#1a2030 38%,#2b3a2c 62%,#3a4a3a 78%,#5a4a38 100%)}
.hero-copy{left:112px;top:130px;color:var(--white)}
.hero-copy h1{font-size:44px;font-weight:700;line-height:1.18;width:470px}
.hero-list{list-style:none;margin-top:26px}
.hero-list li{display:flex;align-items:center;gap:14px;font-size:19px;font-weight:500;margin-bottom:12px}
.hero-list .dot{width:20px;height:20px;border-radius:50%;background:var(--white)}
.hero-copy .btn{margin-top:110px}

/* how it works */
.how{top:720px;left:0;width:1200px;height:648px}
.how .section-title{position:absolute;top:100px;width:100%}
.step{width:230px;text-align:center;top:230px}
.step-icon{width:62px;height:62px;border-radius:10px;background:var(--white);box-shadow:0 6px 18px rgba(20,29,79,.16);margin:0 auto;display:flex;align-items:center;justify-content:center}
.step-icon.on{background:var(--navy)}
.step h3{font-size:14px;font-weight:700;margin-top:22px}
.step p{font-size:11px;color:var(--muted);line-height:1.5;margin-top:8px}

/* product */
.product{top:1368px;left:0;width:1200px;height:372px;background:var(--tint)}
.product-shot{left:80px;top:60px;width:450px;height:250px;border-radius:8px;background:linear-gradient(135deg,#0f1429,#2a3560 60%,#1b2b4a)}
.product-copy{left:640px;top:50px;width:460px}
.product-copy h2,.about-copy h2{font-size:46px;font-weight:300}
.product-copy h2 b,.about-copy h2 b{font-weight:700}
.sub{font-size:15px;font-weight:700;color:var(--primary);margin-top:8px;line-height:1.4}
.body-text{font-size:12px;color:var(--muted);line-height:1.65;margin-top:14px}
.product-copy .btn,.about-copy .btn{margin-top:24px}

/* benefits */
.benefits{top:1740px;left:0;width:1200px;height:620px}
.benefits .section-title{position:absolute;top:80px;width:100%}
.core{left:500px;top:220px;width:200px;height:200px;border-radius:22px;background:var(--navy);color:var(--white);display:flex;align-items:center;justify-content:center;font-size:26px;font-weight:700}
.bicon{width:46px;height:46px;border-radius:50%;background:var(--navy);display:flex;align-items:center;justify-content:center}
.blabel{font-size:16px;font-weight:600;line-height:1.35;width:230px}
.blabel.r{text-align:right}

/* about */
.about{top:2360px;left:0;width:1200px;height:488px;background:var(--tint)}
.about-copy{left:120px;top:70px;width:420px}
.about-shot{left:640px;top:0;width:560px;height:488px;background:linear-gradient(160deg,#0b1a3a,#1d3f72 45%,#0c1630)}

/* packages */
.packages{top:2848px;left:0;width:1200px;height:872px;background:var(--tint-soft)}
.packages .section-title{position:absolute;top:90px;width:100%}
.packages .lead{position:absolute;top:156px;width:100%;text-align:center;font-size:15px;font-weight:600;color:var(--muted)}
.price-table{left:120px;top:208px;width:940px;border-collapse:collapse;background:var(--white);font-size:11px}
.price-table th,.price-table td{border:1px solid var(--line);height:42px;padding:0 14px}
.price-table th{text-align:center;font-weight:700;font-size:13px}
.price-table th small{display:block;font-size:20px;font-weight:700;margin-top:4px}
.price-table th em{display:block;font-style:normal;font-weight:400;font-size:9px;opacity:.8}
.price-table .feat-head{text-align:left;background:#eef0f6;font-size:11px}
.price-table .club{background:var(--navy);color:var(--white);width:160px}
.price-table .agency{background:#c9d4f2;color:var(--navy);width:180px}
.price-table .player{background:var(--primary);color:var(--white);width:180px}
.price-table td{text-align:center;color:var(--ink)}
.price-table td:first-child{text-align:left;font-weight:500}
.tick{color:var(--primary);font-weight:700;font-size:14px}
.notes{left:120px;top:772px;width:940px}
.notes h4{font-size:16px;font-weight:700}
.notes ul{list-style:none;display:flex;gap:70px;margin-top:8px;font-size:12px;color:var(--muted)}
.notes li::before{content:"✓ ";color:var(--primary);font-weight:700}

/* cta */
.cta{top:3720px;left:112px;width:976px;height:330px;border-radius:8px;background:var(--navy-deep);overflow:hidden}
.cta-shot{right:0;top:0;width:460px;height:330px;background:radial-gradient(ellipse at 60% 70%,#1d7a48 0%,#0e3a2a 40%,var(--navy-deep) 80%)}
.cta-copy{left:28px;top:60px;width:430px;color:var(--white)}
.cta-copy h2{font-size:40px;font-weight:700;line-height:1.18}
.cta-copy p{font-size:13px;line-height:1.55;margin-top:14px;opacity:.85}
.cta-copy .btn{margin-top:22px}

/* footer */
.site-footer{top:4120px;left:0;width:1200px;height:412px;background:var(--navy-deep);color:var(--white)}
.site-footer .brand{position:absolute;left:120px;top:70px;font-size:26px}
.site-footer .brand-square{background:var(--white);width:36px;height:36px}
.socials{left:120px;top:140px;display:flex;gap:10px}
.socials span{width:26px;height:26px;border-radius:4px;background:var(--white)}
.fcol{top:70px}
.fcol h5{font-size:15px;font-weight:700;margin-bottom:14px}
.fcol li{list-style:none;font-size:12px;margin-bottom:8px;opacity:.9}
.contact li{display:flex;align-items:center;gap:10px}
.contact i{width:18px;height:18px;border-radius:50%;background:var(--white);flex:none}
.copyright{bottom:0;left:0;width:1200px;height:44px;border-top:1px solid rgba(255,255,255,.15);font-size:11px;display:flex;align-items:center;justify-content:center;opacity:.85}
</style>
</head>
<body>

<header class="site-header abs">
  <div class="brand"><span class="brand-square"></span>Merivantalo</div>
  <nav class="site-nav">
    <span class="active">Home</span><span>Product</span><span>Packages</span><span>How It Works</span><span>FAQ's</span>
    <span class="btn btn-navy">Contact</span>
  </nav>
</header>

<section class="hero abs" role="img" aria-label="Desk with a monitor showing a football scouting dashboard and pitch tactics view">
  <div class="hero-copy abs">
    <h1>Professional Football Scouting Reports</h1>
    <ul class="hero-list">
      <li><span class="dot"></span>Structured</li>
      <li><span class="dot"></span>Precise</li>
      <li><span class="dot"></span>Executive Ready</li>
    </ul>
    <span class="btn btn-white">View Demo Report</span>
  </div>
</section>

<section class="how abs">
  <h2 class="section-title">How <b>It Works</b></h2>
  <svg class="abs" style="left:0;top:200px" width="1200" height="120" viewBox="0 0 1200 120" fill="none" stroke="#9aa3bf" stroke-width="1.5" stroke-dasharray="5 5">
    <path d="M195 61 C 260 20, 360 20, 425 61"/>
    <path d="M510 61 C 580 100, 660 100, 725 61"/>
    <path d="M810 61 C 880 20, 960 20, 1020 61"/>
  </svg>
  <div class="step abs" style="left:35px">
    <div class="step-icon"><svg width="26" height="26" viewBox="0 0 24 24" fill="none" stroke="#141d4f" stroke-width="2"><path d="M3 11 12 4l9 7v9H3z"/><path d="M9 20v-6h6v6"/></svg></div>
    <h3>Install the Software</h3>
    <p>Download Merivantalo after purchase and install it locally on your desktop.</p>
  </div>
  <div class="step abs" style="left:350px">
    <div class="step-icon"><svg width="26" height="26" viewBox="0 0 24 24" fill="none" stroke="#141d4f" stroke-width="2"><ellipse cx="12" cy="5" rx="8" ry="3"/><path d="M4 5v14c0 1.7 3.6 3 8 3s8-1.3 8-3V5M4 12c0 1.7 3.6 3 8 3s8-1.3 8-3"/></svg></div>
    <h3>Input Player Evaluation Data</h3>
    <p>Enter structured player information using guided fields.</p>
  </div>
  <div class="step abs" style="left:655px">
    <div class="step-icon on"><svg width="26" height="26" viewBox="0 0 24 24" fill="#fff"><circle cx="12" cy="7" r="3"/><circle cx="5" cy="10" r="2"/><circle cx="19" cy="10" r="2"/><path d="M7 20c0-3 2-6 5-6s5 3 5 6z"/></svg></div>
    <h3>Review Structured Report Layout</h3>
    <p>Merivantalo automatically formats your input into a clean, executive A4 layout.</p>
  </div>
  <div class="step abs" style="left:945px">
    <div class="step-icon"><svg width="26" height="26" viewBox="0 0 24 24" fill="none" stroke="#141d4f" stroke-width="2"><path d="M6 2h9l5 5v15H6z"/><path d="M15 2v5h5M9 13h8M9 17h6"/></svg></div>
    <h3>Generate Executive A4 PDF</h3>
    <p>Export a ready-to-share PDF report instantly.</p>
  </div>
</section>

<section class="product abs">
  <div class="product-shot abs" role="img" aria-label="Laptop and tablet showing the scouting report software interface"></div>
  <div class="product-copy abs">
    <h2>Our <b>Product</b></h2>
    <p class="sub">Professional Football Scouting Report Generation Software</p>
    <p class="body-text">Merivantalo is a standalone desktop application designed to generate structured, executive-ready A4 scouting reports for professional football organizations.</p>
    <p class="body-text">It provides a standardized framework for documenting player evaluations with precision, consistency and clarity.</p>
    <span class="btn btn-navy">Buy a Demo</span>
  </div>
</section>

<section class="benefits abs">
  <h2 class="section-title">Our <b>Benefits</b></h2>
  <div class="core abs">Merivantalo</div>
  <div class="blabel r abs" style="left:150px;top:230px">Standardized Reporting Across Departments</div>
  <div class="bicon abs" style="left:400px;top:228px"><svg width="20" height="20" viewBox="0 0 24 24" fill="none" stroke="#fff" stroke-width="2"><path d="M4 6h16M4 12h16M4 18h10"/></svg></div>
  <div class="blabel r abs" style="left:170px;top:360px">Executive-Ready Presentation</div>
  <div class="bicon abs" style="left:420px;top:350px"><svg width="20" height="20" viewBox="0 0 24 24" fill="none" stroke="#fff" stroke-width="2"><circle cx="12" cy="12" r="8"/><circle cx="12" cy="12" r="3"/></svg></div>
  <div class="bicon abs" style="left:755px;top:228px"><svg width="20" height="20" viewBox="0 0 24 24" fill="none" stroke="#fff" stroke-width="2"><circle cx="12" cy="12" r="8"/><path d="M12 7v5l3 2"/></svg></div>
  <div class="blabel abs" style="left:820px;top:230px">Time Efficiency Without Compromise</div>
  <div class="bicon abs" style="left:735px;top:350px"><svg width="20" height="20" viewBox="0 0 24 24" fill="none" stroke="#fff" stroke-width="2"><path d="M12 3 5 6v6c0 4 3 7 7 9 4-2 7-5 7-9V6z"/></svg></div>
  <div class="blabel abs" style="left:800px;top:362px">Secure Offline Operation</div>
  <div class="bicon abs" style="left:577px;top:445px"><svg width="20" height="20" viewBox="0 0 24 24" fill="none" stroke="#fff" stroke-width="2"><circle cx="12" cy="9" r="5"/><path d="M9 13l-2 8 5-3 5 3-2-8"/></svg></div>
  <div class="blabel abs" style="left:485px;top:505px;text-align:center">Professional Credibility</div>
</section>

<section class="about abs">
  <div class="about-copy abs">
    <h2>About <b>Us</b></h2>
    <p class="sub">Structured Intelligence for Professional Football</p>
    <p class="body-text">Merivantalo was created to bring structure, consistency and executive-level presentation to professional football scouting documentation.</p>
    <p class="body-text">In modern football organizations, player evaluation is detailed and analytical — but reporting standards are often inconsistent. Merivantalo was built to solve that problem.</p>
    <span class="btn btn-navy">Read More</span>
  </div>
  <div class="about-shot abs" role="img" aria-label="Analyst workstation with multiple monitors showing performance data"></div>
</section>

<section class="packages abs">
  <h2 class="section-title">Our <b>Packages</b></h2>
  <p class="lead">Structured Solution For Different Professional Needs</p>
  <table class="price-table abs">
    <tr>
      <th class="feat-head">Feature</th>
      <th class="club">Club Edition<small>€799</small><em>One-time purchase</em></th>
      <th class="agency">Agency Edition<small>€699</small><em>One-time purchase</em></th>
      <th class="player">Player Edition<small>€299</small><em>One-time purchase</em></th>
    </tr>
    <tr><td>One-Time Purchase</td><td class="tick">✓</td><td class="tick">✓</td><td class="tick">✓</td></tr>
    <tr><td>Standalone Desktop Software</td><td class="tick">✓</td><td class="tick">✓</td><td class="tick">✓</td></tr>
    <tr><td>Structured Evaluation Framework</td><td class="tick">✓</td><td class="tick">✓</td><td class="tick">✓</td></tr>
    <tr><td>Executive A4 PDF Export</td><td class="tick">✓</td><td class="tick">✓</td><td class="tick">✓</td></tr>
    <tr><td>Multi-Scout Profiles</td><td class="tick">✓</td><td class="tick">✓</td><td>—</td></tr>
    <tr><td>Organization Branding on Reports</td><td class="tick">✓</td><td class="tick">✓</td><td>Limited</td></tr>
    <tr><td>Advanced Evaluation Fields</td><td class="tick">✓</td><td class="tick">✓</td><td>—</td></tr>
    <tr><td>Custom Rating Scales</td><td class="tick">✓</td><td class="tick">✓</td><td>Limited</td></tr>
    <tr><td>Report Template Variations</td><td>Professional Clubs</td><td>Player Agencies</td><td>Individual Players</td></tr>
    <tr><td>Designed For</td><td>Professional Clubs</td><td>Player Agencies</td><td>Individual Players</td></tr>
  </table>
  <div class="notes abs">
    <h4>One-Time Purchase. No Recurring Fees.</h4>
    <ul><li>No subscription</li><li>No monthly payments</li><li>Full offline operation</li></ul>
  </div>
</section>

<section class="cta abs">
  <div class="cta-shot abs" role="img" aria-label="Laptop showing a football pitch with a glowing green ball"></div>
  <div class="cta-copy abs">
    <h2>Standardize Your Scouting Documentation</h2>
    <p>Generate structured, executive-ready A4 scouting reports with professional consistency.</p>
    <span class="btn btn-white">Purchase Software</span>
  </div>
</section>

<footer class="site-footer abs">
  <div class="brand"><span class="brand-square"></span>Merivantalo</div>
  <div class="socials abs"><span></span><span></span><span></span><span></span></div>
  <div class="fcol abs" style="left:512px"><h5>Quick Links</h5><ul><li>Home</li><li>Product</li><li>Packages</li><li>How It Works</li><li>FAQ's</li><li>Contact</li></ul></div>
  <div class="fcol abs" style="left:680px"><h5>Other Links</h5><ul><li>Privacy Policy</li><li>Terms &amp; Conditions</li><li>Disclaimer</li><li>FAQ's</li><li>Support</li><li>Help</li></ul></div>
  <div class="fcol contact abs" style="left:880px"><h5>Contact Info</h5><ul><li><i></i>Kalliokatu 14, Tampere</li><li><i></i>+358 40 555 0199</li><li><i></i>hello@merivantalo-reports.test</li></ul></div>
  <div class="copyright abs">Copyright © 2025 Merivantalo. All rights reserved.</div>
</footer>

</body>
</html>
```